Veldmark Supplies Business Card

Professional business card that stand out to our potential customers. Front and back with clean modern design

Industry/Entity Type

Oil and gas

Contact Information for Business Card

Name, address, website , office phone and cell number

Requirements
Must have
• Editable files for each employee

```html
<!DOCTYPE html>
<html lang="en">
<head>
<meta charset="utf-8">
<title>Veldmark Supplies Business Card</title>
<link href="https://fonts.googleapis.com/css2?family=Poppins:wght@400;600&display=swap" rel="stylesheet">
<style>
  :root {
    --brand-blue: #12b0d2;
    --brand-red: #ed2426;
    --card-white: #ffffff;
    --backdrop: #e3e7e9;
  }
  * { box-sizing: border-box; margin: 0; padding: 0; }
  html, body {
    width: 1200px; height: 960px; overflow: hidden;
    background: var(--backdrop);
    font-family: "Poppins", sans-serif;
  }
  .card {
    position: absolute;
    left: 249px;
    width: 702px;
    height: 400px;
    overflow: hidden;
  }
  .card-front { top: 60px; background: var(--brand-blue); }
  .card-back { top: 500px; background: var(--card-white); }

  .front-brand {
    position: absolute;
    left: 0; right: 0; top: 178px;
    display: flex; align-items: center; justify-content: center; gap: 14px;
  }
  .brand-square {
    width: 30px; height: 30px; background: var(--brand-red);
  }
  .front-brand .brand-name {
    color: var(--card-white);
    font-weight: 600; font-size: 34px; letter-spacing: 0.5px;
  }

  .back-brand {
    position: absolute; left: 24px; top: 150px;
    display: flex; align-items: center; gap: 10px;
  }
  .back-brand .brand-square { width: 20px; height: 20px; background: var(--brand-blue); }
  .back-brand .brand-name {
    color: var(--brand-red); font-weight: 600; font-size: 21px;
  }

  .person {
    position: absolute; right: 27px; top: 22px; text-align: right;
  }
  .person-name {
    color: var(--brand-red); font-size: 33px; line-height: 1.1; font-weight: 400;
  }
  .person-name .first { font-weight: 600; }
  .person-title {
    color: var(--brand-blue); font-size: 18px; line-height: 1.2; margin-top: 2px;
  }
  .accent-bar {
    position: absolute; right: 0; top: 32px; width: 19px; height: 54px;
    background: var(--brand-blue);
  }

  .address {
    position: absolute; left: 23px; top: 211px;
    color: var(--brand-blue); font-size: 18px; line-height: 24px; letter-spacing: 0.4px;
  }

  .contact-band {
    position: absolute; left: 0; right: 0; top: 273px; bottom: 0;
    background: var(--brand-red);
  }
  .contact-list {
    list-style: none; position: absolute; left: 26px; top: 12px;
  }
  .contact-list li {
    display: flex; align-items: center; gap: 12px;
    color: var(--card-white); font-size: 18px; line-height: 24px;
  }
  .contact-list svg { width: 18px; height: 18px; flex: none; }
</style>
</head>
<body>

<section class="card card-front">
  <div class="front-brand">
    <span class="brand-square"></span>
    <span class="brand-name">Veldmark Supplies</span>
  </div>
</section>

<section class="card card-back">
  <div class="back-brand">
    <span class="brand-square"></span>
    <span class="brand-name">Veldmark Supplies</span>
  </div>

  <div class="person">
    <p class="person-name"><span class="first">Marta</span> Kolarova</p>
    <p class="person-title">Co-Founder &amp; CEO</p>
  </div>
  <div class="accent-bar"></div>

  <address class="address" style="font-style:normal">
    418 Larkfield Road,<br>Odessa Creek, TX 79760
  </address>

  <div class="contact-band">
    <ul class="contact-list">
      <li>
        <svg viewBox="0 0 24 24" fill="none" stroke="#9fe3f2" stroke-width="2" stroke-linecap="round" stroke-linejoin="round"><path d="M5 3h4l2 5-2.5 1.5a11 11 0 0 0 6 6L16 13l5 2v4a2 2 0 0 1-2 2A17 17 0 0 1 3 5a2 2 0 0 1 2-2z"/></svg>
        (432) 555-0147
      </li>
      <li>
        <svg viewBox="0 0 24 24" fill="none" stroke="#9fe3f2" stroke-width="2"><rect x="6" y="2" width="12" height="20" rx="2"/><line x1="10" y1="18" x2="14" y2="18"/></svg>
        (432) 555-0182
      </li>
      <li>
        <svg viewBox="0 0 24 24" fill="none" stroke="#9fe3f2" stroke-width="2"><circle cx="12" cy="12" r="10"/><path d="M2 12h20M12 2a15 15 0 0 1 0 20M12 2a15 15 0 0 0 0 20"/></svg>
        www.veldmark.com
      </li>
      <li>
        <svg viewBox="0 0 24 24" fill="none" stroke="#9fe3f2" stroke-width="2" stroke-linejoin="round"><rect x="3" y="6" width="18" height="14" rx="1"/><path d="M3 7l9 7 9-7"/></svg>
        info@veldmark.com
      </li>
    </ul>
  </div>
</section>

</body>
</html>
```